Heater product information sheets

I need the two product information sheets organized and laid out in a clean, easy to read attractive manner. These sheets are to advertise propane heaters for outdoor use and for wholesale to propane distributors, restaurants and homeowners that need to have propane heat as the winter ends and spring begins. They will be used for chilly evenings when people want to be outside eating, drinking and being social.

Target Market(s)

Restaurants, hospitality industry, special events, party rental companies, home owners with backyards

Font styles to use
Sans Serif

Requirements
Must have
• My logo in the document instead of t. Marlow and company
Nice to have
• I would like to see Fire illustrated coming up the heaters and on the round glass, show it up the middle of the glass tube propane heater.

```html
<!DOCTYPE html>
<html lang="en">
<head>
<meta charset="utf-8">
<title>Propane Heater Product Sheets</title>
<link href="https://fonts.googleapis.com/css2?family=Archivo+Black&family=Arimo:wght@400;700&display=swap" rel="stylesheet">
<style>
:root{
  --orange:#f47a2a;
  --ink:#111111;
  --dark:#1c1c1c;
  --paper:#ffffff;
  --mist:#ececec;
  --stage:#e4e4e4;
  --text:#1a1a1a;
}
*{margin:0;padding:0;box-sizing:border-box}
html,body{width:1200px;height:796px;overflow:hidden;background:var(--stage)}
body{position:relative;font-family:"Arimo",Arial,sans-serif;color:var(--text)}
.sheet{position:absolute;top:73px;width:500px;height:650px;background:linear-gradient(160deg,var(--paper) 40%,var(--mist));overflow:hidden;box-shadow:0 4px 14px rgba(0,0,0,.25)}
.sheet--outdoor{left:86px}
.sheet--glass{left:629px}
.shapes{position:absolute;inset:0;width:100%;height:100%}
.abs{position:absolute}
.title{font-family:"Archivo Black",Arial,sans-serif;color:var(--ink);letter-spacing:.5px}
.title .accent{color:var(--orange)}
.pill{position:absolute;background:var(--orange);border-radius:0 13px 13px 13px;font-family:"Archivo Black",Arial,sans-serif;color:#fff;display:flex;align-items:center;padding-left:14px;letter-spacing:1px}
.pill--dark-text{color:var(--ink);padding-left:20px}
.spec-list{list-style:none;font-size:8.7px;letter-spacing:.6px;line-height:14px;text-transform:uppercase}
.spec-list li::before{content:"•";margin-right:4px}
.detail-list{list-style:none;font-size:10px;line-height:14.3px}
.detail-list li{padding-left:9px;position:relative}
.detail-list li::before{content:"•";color:var(--orange);position:absolute;left:0}
.detail-list .indent::before{content:none}
.heading{font-family:"Archivo Black",Arial,sans-serif;font-size:16px;letter-spacing:1px;color:var(--ink)}
.offers{right:28px;top:24px;text-align:right;color:#fff;font-size:9px;font-weight:700;line-height:11px;text-transform:uppercase;list-style:none}
.offers li{display:flex;align-items:center;justify-content:flex-end;gap:6px;margin-bottom:9px}
.contact{left:26px;top:570px;color:#fff;font-size:9px;line-height:13.5px}
.contact .label{font-weight:700;letter-spacing:.3px}
.contact .company{color:var(--orange);font-weight:700;text-transform:uppercase;margin-bottom:4px}
.contact .row{display:flex;align-items:center;gap:6px;letter-spacing:.4px}
.note{left:293px;top:543px;font-size:8.3px;line-height:10.8px}
.note h3{font-family:"Archivo Black",Arial,sans-serif;color:var(--orange);font-size:18px;line-height:20px;letter-spacing:1px;margin-bottom:2px}
.product{border-radius:6px}
</style>
</head>
<body>

<section class="sheet sheet--outdoor">
  <svg class="shapes" viewBox="0 0 500 650" preserveAspectRatio="none" aria-hidden="true">
    <path d="M0 0H500V192C400 122 200 42 0 31Z" fill="var(--dark)"/>
    <path d="M0 31C200 42 400 122 500 192V207C400 135 200 78 0 67Z" fill="var(--orange)"/>
    <path d="M0 547C150 552 270 590 320 615C350 632 370 645 380 650H0Z" fill="var(--dark)"/>
    <path d="M300 650C380 640 450 620 500 600V625C460 640 420 648 400 650Z" fill="var(--orange)"/>
    <path d="M400 650C440 646 470 638 500 625V650Z" fill="var(--dark)"/>
  </svg>

  <ul class="abs offers">
    <li>Rentals for live events <svg width="10" height="10" viewBox="0 0 10 10"><circle cx="5" cy="5" r="5" fill="var(--orange)"/><path d="M2.6 5.2l1.6 1.5 3.2-3.3" stroke="#fff" stroke-width="1.3" fill="none"/></svg></li>
    <li><span>Rentals for restaurants<br>&amp; catering halls</span> <svg width="10" height="10" viewBox="0 0 10 10"><circle cx="5" cy="5" r="5" fill="var(--orange)"/><path d="M2.6 5.2l1.6 1.5 3.2-3.3" stroke="#fff" stroke-width="1.3" fill="none"/></svg></li>
    <li><span>Purchase for your home<br>or business</span> <svg width="10" height="10" viewBox="0 0 10 10"><circle cx="5" cy="5" r="5" fill="var(--orange)"/><path d="M2.6 5.2l1.6 1.5 3.2-3.3" stroke="#fff" stroke-width="1.3" fill="none"/></svg></li>
  </ul>

  <h1 class="abs title" style="left:26px;top:91px;font-size:38px;line-height:47px">OUTDOOR<br>PROPANE<br><span class="accent">HEATER</span></h1>

  <div class="pill" style="left:22px;top:243px;width:219px;height:24px;font-size:17px">SPECIFICATIONS</div>
  <ul class="abs spec-list" style="left:26px;top:274px">
    <li>Powerful 48,000 BTU</li>
    <li>Black powder coated finish</li>
    <li>Uses 20 lbs. propane tank</li>
    <li>CE, GS, AGA, CSA, with ETL certificate<br>&nbsp;&nbsp;and RoHS approved</li>
  </ul>

  <h2 class="abs heading" style="left:29px;top:349px">ADDITIONAL DETAILS</h2>
  <ul class="abs detail-list" style="left:26px;top:371px">
    <li>Commercial Quality</li>
    <li>For Outdoor Use Only</li>
    <li>Conforms to ANSI STD Z83.26-2014 Certified</li>
    <li class="indent">to CSA STD 2.37-2014 Gas- fired outdoor infrared patio heaters</li>
    <li>Safety Auto Shut Off Switch</li>
    <li>Thermostatic Control</li>
    <li>Base Diameter 17” - Anti-Tip Design</li>
    <li>Standard Wheels - Tilt &amp; Move</li>
    <li>Run time: 8-10 hours with standard 20 lbs. Propane tank</li>
    <li>88” Tall</li>
    <li>Heating Area: 200 sq. ft</li>
  </ul>

  <div class="abs product" role="img" aria-label="Product photo of a black mushroom-top outdoor propane patio heater" style="left:336px;top:204px;width:128px;height:334px;background:linear-gradient(180deg,#cfcfcf 0%,#8a8a8a 18%,#2a2a2a 55%,#111 100%)"></div>

  <div class="abs note">
    <h3>NOTE</h3>
    <p>Price: Starting at $250 each</p>
    <p>Assembly &amp; Delivery available upon request</p>
    <p>Discounts for large quantity orders</p>
  </div>

  <div class="abs contact">
    <p class="label">TO RENT OR PURCHASE:</p>
    <p class="company">T. Marlow &amp; Company</p>
    <p class="row"><svg width="9" height="9" viewBox="0 0 10 10"><circle cx="5" cy="5" r="5" fill="var(--orange)"/><path d="M3 2.5l1.2 1.6-.6.7c.4.8 1 1.4 1.6 1.7l.7-.6 1.6 1.1-.5 1C4.8 7.8 2.4 5.4 2.2 3z" fill="#fff"/></svg>555-014-2286</p>
    <p class="row"><svg width="9" height="9" viewBox="0 0 10 10"><circle cx="5" cy="5" r="5" fill="var(--orange)"/><rect x="2.5" y="3.3" width="5" height="3.4" fill="none" stroke="#fff" stroke-width=".8"/><path d="M2.5 3.4l2.5 2 2.5-2" stroke="#fff" stroke-width=".8" fill="none"/></svg>sam@marlowrentals.com</p>
    <p class="row"><svg width="9" height="9" viewBox="0 0 10 10"><circle cx="5" cy="5" r="5" fill="var(--orange)"/><path d="M5 2a2 2 0 0 1 2 2c0 1.5-2 4-2 4S3 5.5 3 4a2 2 0 0 1 2-2z" fill="#fff"/></svg>42 Foundry Lane Millbrook, NJ 07000</p>
  </div>
</section>

<section class="sheet sheet--glass">
  <div class="abs" role="img" aria-label="Photo of a woman relaxing on a patio with wicker furniture, a dog and a glass tube heater beside a house" style="left:0;top:0;width:500px;height:230px;background:linear-gradient(170deg,#bfc4c4 0%,#8d8a82 45%,#5e5448 100%);clip-path:path('M0 0H500V200C400 218 300 220 200 214C120 202 50 152 0 98Z')"></div>

  <svg class="shapes" viewBox="0 0 500 650" preserveAspectRatio="none" aria-hidden="true">
    <path d="M0 98C50 152 120 202 200 214C300 220 400 218 500 200V214C350 236 150 238 0 240Z" fill="var(--dark)"/>
    <path d="M120 202C250 224 400 218 500 198V228C400 246 250 242 120 202Z" fill="var(--orange)"/>
    <path d="M0 547C150 552 270 590 320 615C350 632 370 645 380 650H0Z" fill="var(--dark)"/>
    <path d="M300 650C380 640 450 622 500 606V628C460 641 420 648 400 650Z" fill="var(--orange)"/>
    <path d="M400 650C440 646 470 639 500 628V650Z" fill="var(--dark)"/>
  </svg>

  <h1 class="abs title" style="left:30px;top:240px;font-size:29px;line-height:30px">GLASS TUBE<br>PROPANE<br><span class="accent">HEATERS</span></h1>

  <div class="pill pill--dark-text" style="left:17px;top:335px;width:220px;height:25px;font-size:14px">ADDITIONAL DETAILS</div>
  <ul class="abs detail-list" style="left:32px;top:369px;font-size:9.3px;line-height:14.7px">
    <li>Commercial Quality</li>
    <li>For Outdoor Use Only</li>
    <li>Conforms to ANSI STD Z83.26-2014 Certified to</li>
    <li class="indent">CSA STD 2.37-2014 Gas- fired outdoor infrared patio heaters</li>
    <li>Safety Auto Shut Off Switch</li>
    <li>Thermostatic Control</li>
    <li>Base Diameter 17” - Anti-Tip Design</li>
    <li>Standard Wheels - Tilt &amp; Move</li>
    <li>Run time: 8-10 hours with standard 20 lbs. Propane tank</li>
    <li>96” Tall</li>
    <li>Heating Area: 200 sq. ft</li>
  </ul>

  <div class="abs product" role="img" aria-label="Product photo of a black glass tube propane patio heater with a round top cap" style="left:318px;top:160px;width:110px;height:332px;background:linear-gradient(180deg,#bdbdbd 0%,#d9d9d9 15%,#e6e6e6 45%,#222 62%,#111 100%)"></div>

  <div class="pill" style="left:281px;top:506px;width:198px;height:23px;font-size:15px">SPECIFICATIONS</div>
  <ul class="abs spec-list" style="left:286px;top:537px;font-size:8.5px;line-height:13.8px">
    <li>Powerful 48,000 BTU</li>
    <li>Black powder coated finish</li>
    <li>Uses 20 lbs. propane tank</li>
    <li>CE, GS, AGA, CSA, with ETL certificate<br>&nbsp;&nbsp;and RoHS approved</li>
  </ul>

  <div class="abs contact">
    <p class="label">TO RENT OR PURCHASE:</p>
    <p class="company">T. Marlow &amp; Company</p>
    <p class="row"><svg width="9" height="9" viewBox="0 0 10 10"><circle cx="5" cy="5" r="5" fill="var(--orange)"/><path d="M3 2.5l1.2 1.6-.6.7c.4.8 1 1.4 1.6 1.7l.7-.6 1.6 1.1-.5 1C4.8 7.8 2.4 5.4 2.2 3z" fill="#fff"/></svg>555-014-2286</p>
    <p class="row"><svg width="9" height="9" viewBox="0 0 10 10"><circle cx="5" cy="5" r="5" fill="var(--orange)"/><rect x="2.5" y="3.3" width="5" height="3.4" fill="none" stroke="#fff" stroke-width=".8"/><path d="M2.5 3.4l2.5 2 2.5-2" stroke="#fff" stroke-width=".8" fill="none"/></svg>sam@marlowrentals.com</p>
    <p class="row"><svg width="9" height="9" viewBox="0 0 10 10"><circle cx="5" cy="5" r="5" fill="var(--orange)"/><path d="M5 2a2 2 0 0 1 2 2c0 1.5-2 4-2 4S3 5.5 3 4a2 2 0 0 1 2-2z" fill="#fff"/></svg>42 Foundry Lane Millbrook, NJ 07000</p>
  </div>
</section>

</body>
</html>
```